BRN website video quote promotion tiles

We are promoting vehicle leasing by video, which contains several quotation examples imported from the video. We must re-vamp the quotation tiles, contact boxes, and contact form. The first tile is generated from the video, so this must be a separate project. We are looking for a welcoming, professional flow and leave color choices to design with an emphasis on communication prompts, and additional prompts in the design would be welcome.

Target Market(s)

Any Customer interaction from the tile quotes, contact, call, message,

Industry/Entity Type

vehicle leasing

Coding

Coded - Design and coding required

Number of Pages Required

1 page

Colors

Designer to choose colors to be used in the design.

Requirements
Must have
• emphasis on point of contact and visual impact on quote tile excluding main one
Should not have
• changes to the quote structure as these imported from video pricing no changes to main image as this template which can addressed as separate project

```html
<!DOCTYPE html>
<html lang="en">
<head>
<meta charset="utf-8">
<title>BRN quote tiles and contact form</title>
<link href="https://fonts.googleapis.com/css2?family=Poppins:wght@400;500;600;700&display=swap" rel="stylesheet">
<style>
:root{
  --orange:#eb7e26;
  --orange-tile:#e0823a;
  --red:#d40f0f;
  --green:#3a9a14;
  --ink:#333;
  --line:#e4e4e4;
  --field:#f4f4f4;
  --white:#fff;
}
*{box-sizing:border-box;margin:0;padding:0}
html,body{width:1200px;height:1156px;overflow:hidden;background:var(--white);font-family:'Poppins',sans-serif;color:var(--ink)}
.canvas{position:relative;width:1200px;height:1156px}
.abs{position:absolute}
.tile{position:absolute;top:61px;height:254px;border:1px solid var(--line);border-radius:16px;background:var(--white)}
.tile-title{font-weight:700;color:var(--orange);font-size:21px;letter-spacing:-.2px;line-height:1.2}
.price-pill{border:2px solid var(--orange);border-radius:20px;color:var(--orange);font-weight:600;display:flex;align-items:center;justify-content:center}
.terms{font-size:14px;color:var(--ink)}
.not-maintained{font-weight:600;color:var(--red);font-size:15px}
.btn{position:absolute;display:flex;align-items:center;justify-content:center;gap:8px;border-radius:24px;font-weight:600;font-size:16px;white-space:nowrap}
.btn-soft{background:var(--field);color:var(--orange)}
.btn-green{background:var(--green);color:var(--white)}
.btn-soft-green{background:var(--field);color:var(--green)}

.tile-a{left:45px;width:291px;text-align:center}
.tile-b{left:357px;width:324px;top:62px;height:253px;background:var(--orange-tile);border:none;border-radius:0;color:var(--white)}
.tile-c{left:704px;width:450px}

.form-panel{position:absolute;left:44px;top:349px;width:1112px;height:748px;border-radius:18px;overflow:hidden}
.form-head{height:90px;background:var(--orange);display:flex;align-items:center;justify-content:space-between;padding:0 40px 0 31px}
.form-head h2{color:var(--white);font-size:21px;font-weight:600;letter-spacing:.1px}
.form-backdrop{position:absolute;left:0;top:90px;width:1112px;height:658px;background:linear-gradient(135deg,#c9dbea 0%,#eef3f8 28%,#ffffff 55%,#eef3f8 75%,#8fb2d2 100%)}
.form-card{position:absolute;left:40px;top:138px;width:1034px;height:564px;background:var(--white);border-radius:12px}
.label{position:absolute;font-size:16px;color:var(--ink);line-height:20px}
.field{position:absolute;height:56px;width:426px;background:var(--field);border-radius:28px;display:flex;align-items:center;gap:6px;padding-left:26px;font-size:17px;color:var(--ink)}
.field svg{flex:none}
.field-message{height:122px;width:872px;align-items:flex-start;padding-top:18px}
.submit{position:absolute;left:80px;top:458px;width:142px;height:53px;border-radius:27px;background:var(--green);color:var(--white);font-weight:700;font-size:17px;display:flex;align-items:center;justify-content:center;gap:6px;letter-spacing:-.3px}
</style>
</head>
<body>
<div class="canvas">

  <div class="tile tile-a">
    <div class="tile-title abs" style="left:0;right:0;top:34px">CONTRACT HIRE</div>
    <div class="price-pill abs" style="left:81px;top:76px;width:91px;height:32px;font-size:16px">£247.33</div>
    <div class="abs" style="left:180px;top:84px;font-size:11px;font-weight:600">+ VAT</div>
    <div class="terms abs" style="left:0;right:0;top:124px">3 years, 9+35, 10K miles annually</div>
    <div class="not-maintained abs" style="left:0;right:0;top:154px">Not Maintained *</div>
    <div class="btn btn-soft" style="left:23px;top:193px;width:116px;height:33px">Contact Us</div>
    <div class="btn btn-green" style="left:150px;top:193px;width:120px;height:33px;font-size:15px">Message Us</div>
  </div>

  <div class="tile tile-b">
    <div class="abs" style="left:23px;top:18px;font-size:21px;font-weight:700;line-height:31px">CONTRACT<br>HIRE</div>
    <div class="abs" style="left:197px;top:29px;width:105px;height:39px;background:var(--white);color:var(--orange-tile);font-weight:600;font-size:15px;display:flex;align-items:center;justify-content:center">£247.33</div>
    <div class="abs" style="left:23px;top:109px;font-size:14px">3 years, 9+35, 10K miles annually</div>
    <div class="abs" style="left:25px;top:138px;font-size:15px;font-weight:600">Not Maintained *</div>
    <svg class="abs" style="left:31px;top:193px" width="40" height="40" viewBox="0 0 40 40">
      <circle cx="20" cy="20" r="19.5" fill="#fff"/>
      <path d="M14 12.5c.8-.7 1.7-.5 2.1.3l1.3 2.5c.3.6.1 1.3-.4 1.7l-.9.7c.7 1.7 2 3.1 3.7 3.9l.8-.9c.4-.5 1.1-.6 1.7-.3l2.4 1.4c.7.4.9 1.3.3 2l-1.2 1.3c-.7.7-1.7.9-2.6.5-3.9-1.6-6.9-4.7-8.4-8.6-.3-.9 0-1.9.7-2.5z" fill="var(--orange-tile)"/>
    </svg>
    <svg class="abs" style="left:80px;top:193px" width="40" height="40" viewBox="0 0 40 40">
      <rect x="1" y="1" width="38" height="38" rx="19" fill="none" stroke="#fff" stroke-width="2"/>
      <path d="M12 13h16v11h-9l-4 4v-4h-3z" fill="none" stroke="#fff" stroke-width="1.8" stroke-linejoin="round"/>
    </svg>
  </div>

  <div class="tile tile-c">
    <div class="tile-title abs" style="left:22px;top:38px">CONTRACT HIRE</div>
    <div class="price-pill abs" style="left:315px;top:22px;width:113px;height:39px;font-size:19px;border-radius:22px">£247.33</div>
    <div class="abs" style="left:27px;top:91px;font-size:19px">3 years, 9+35, 10K miles annually</div>
    <div class="not-maintained abs" style="left:30px;top:132px;border-bottom:1px solid var(--red);line-height:20px;padding-right:4px">Not Maintained</div>
    <div class="btn btn-soft" style="left:23px;top:179px;width:158px;height:45px">
      <svg width="30" height="28" viewBox="0 0 30 28"><rect x="9" y="8" width="19" height="14" rx="2" fill="none" stroke="var(--orange)" stroke-width="2"/><path d="M9 9l9.5 7 9.5-7" fill="none" stroke="var(--orange)" stroke-width="2"/><path d="M3 4c1-1 2.2-.8 2.7.3l1.6 3c.3.7.1 1.5-.5 2l-1 .8c.8 2 2.4 3.7 4.3 4.6" fill="none" stroke="var(--orange)" stroke-width="2.4" stroke-linecap="round"/></svg>
      Contact Us
    </div>
    <div class="btn btn-soft-green" style="left:196px;top:179px;width:160px;height:45px">
      <svg width="22" height="20" viewBox="0 0 22 20"><path d="M2 2h18v12H9l-5 4v-4H2z" fill="none" stroke="var(--green)" stroke-width="2" stroke-linejoin="round"/></svg>
      Message Us
    </div>
  </div>

  <div class="form-panel">
    <div class="form-head">
      <h2>PLEASE SUBMIT YOUR CONTACT DETAILS</h2>
      <svg width="30" height="30" viewBox="0 0 30 30"><circle cx="15" cy="15" r="15" fill="#fff"/><path d="M10 10l10 10M20 10l-10 10" stroke="var(--orange)" stroke-width="3.4" stroke-linecap="round"/></svg>
    </div>
    <div class="form-backdrop" role="img" aria-label="Soft blue abstract background behind the form"></div>
    <div class="form-card">
      <div class="label" style="left:106px;top:58px">First Name*</div>
      <div class="field" style="left:80px;top:90px">
        <svg width="13" height="15" viewBox="0 0 13 15"><circle cx="6.5" cy="4" r="3.6" fill="#333"/><path d="M0 15c0-4 2.6-6 6.5-6s6.5 2 6.5 6z" fill="#333"/></svg>Sam</div>
      <div class="label" style="left:552px;top:58px">Last Name*</div>
      <div class="field" style="left:526px;top:90px">
        <svg width="13" height="15" viewBox="0 0 13 15"><circle cx="6.5" cy="4" r="3.6" fill="#333"/><path d="M0 15c0-4 2.6-6 6.5-6s6.5 2 6.5 6z" fill="#333"/></svg>Carter</div>

      <div class="label" style="left:106px;top:173px">Email*</div>
      <div class="field" style="left:80px;top:205px">
        <svg width="17" height="13" viewBox="0 0 17 13"><rect x="1" y="1" width="15" height="11" rx="1" fill="none" stroke="#333" stroke-width="2"/><path d="M1 2l7.5 6L16 2" fill="none" stroke="#333" stroke-width="2"/></svg>info@samcarter.com</div>
      <div class="label" style="left:552px;top:173px">Contact Number*</div>
      <div class="field" style="left:526px;top:205px">
        <svg width="15" height="15" viewBox="0 0 15 15"><path d="M2 1c.8-.7 1.7-.5 2.1.3l1.3 2.5c.3.6.1 1.3-.4 1.7l-.9.7c.7 1.7 2 3.1 3.7 3.9l.8-.9c.4-.5 1.1-.6 1.7-.3l2.4 1.4c.7.4.9 1.3.3 2l-1.2 1.3c-.7.7-1.7.9-2.6.5C5.3 12.5 2.3 9.4.8 5.5.5 4.6.8 3.6 1.5 3z" fill="#333"/></svg>+1 (555 0142 777)</div>

      <div class="label" style="left:106px;top:286px">Message*</div>
      <div class="field field-message" style="left:80px;top:318px">
        <svg width="16" height="16" viewBox="0 0 16 16"><path d="M2 14l1-4 8-8 3 3-8 8z" fill="#333"/></svg>Type here......</div>

      <div class="submit">SUBMIT
        <svg width="17" height="17" viewBox="0 0 17 17"><circle cx="8.5" cy="8.5" r="8.5" fill="#fff"/><path d="M4.5 8.5h7M8.5 5l3.5 3.5L8.5 12" fill="none" stroke="var(--green)" stroke-width="2.2" stroke-linecap="round" stroke-linejoin="round"/></svg>
      </div>
    </div>
  </div>

</div>
</body>
</html>
```